Non Profit Company Looking For New Website

The website for Fernvale Quillstone Heritage Society should offer the viewer beautiful photos that inspire condifence and joy and tap into our love of horses.

We would like to see a website that displays trust, quality and confidence. Needs to be responsive and mobile friendly for all browsers and coded for both Android & IOS.

READ ATTACHED WEBSITE TEMPLATE FOR COMPLETE DETAILS ON WHAT WE ARE LOOKING FOR.

Looking for recommmendations if we should use WordPress/WooCommerce for site or Wordpress with Shopify Plug in or just Shopify.

Must be both desktop and mobile friendly with fast page load speed. Need the ability to edit ourselves.

Industry/Entity Type

Non Profit

Coding

Coded - Design and coding required

Number of Pages Required

5+ page

Requirements
Must have
• We would like to see a website that displays trust, quality and confidence. Needs to be responsive and mobile friendly for all browsers and coded for both Android & IOS.

Looking for recommendations if we should use WordPress/WooCommerce for site or Wordpress with Shopify Plug in or just Shopify.

Logo Colour:
Pantone 7621 C

READ TEMPLATE THAT IS ATTACHED
Nice to have
• Like look of this website as a sample:
https://www.quellbrimtorva.com/

Another similar non profit organization
https://pellaworthcindle.com/

```html
<!DOCTYPE html>
<html lang="en">
<head>
<meta charset="utf-8">
<title>Fernvale Quillstone Heritage Society</title>
<link href="https://fonts.googleapis.com/css2?family=Poppins:wght@300;400;500;600&display=swap" rel="stylesheet">
<style>
:root{
  --brand:#b3131f;
  --ink:#1c1c1c;
  --white:#fff;
  --footer:#050505;
  --rule:#c9c9c9;
  --storm:#2a2a30;
  --dust:#b98156;
  --turf:#4a8a36;
}
*{margin:0;padding:0;box-sizing:border-box}
html,body{width:1200px;height:3651px;overflow:hidden}
body{position:relative;font-family:'Poppins',sans-serif;color:var(--ink);background:var(--white)}
.abs{position:absolute}
.center{left:0;width:1200px;text-align:center}

/* hero */
.hero{top:0;left:0;width:1200px;height:662px;
  background:
    radial-gradient(ellipse 70% 45% at 50% 42%,rgba(168,98,58,.75) 0%,rgba(120,70,42,.45) 45%,rgba(0,0,0,0) 75%),
    linear-gradient(to bottom,#25252b 0%,#33302f 18%,#5a3e2e 38%,#7e5236 55%,#a4704b 75%,#c08a60 90%,#b98359 100%)}
.hero-shade{top:0;left:0;width:1200px;height:662px;background:linear-gradient(to bottom,rgba(0,0,0,.25),rgba(0,0,0,0) 30%,rgba(0,0,0,.12) 55%,rgba(0,0,0,0) 75%)}
.brand-card{top:0;left:112px;width:188px;height:173px;background:var(--white);
  border-radius:0 0 44px 44px;display:flex;flex-direction:column;align-items:center;justify-content:center;gap:10px;z-index:3}
.brand-card .dot{width:14px;height:14px;border-radius:50%;background:var(--brand)}
.brand-name{color:var(--brand);font-weight:600;font-size:15px;line-height:1.25;text-align:center;text-transform:uppercase;padding:0 14px}
.nav a{position:absolute;top:86px;color:var(--white);text-decoration:none;font-size:15px;letter-spacing:.3px;white-space:nowrap;z-index:3}
.hero-copy{z-index:3;color:var(--white);text-shadow:0 1px 3px rgba(0,0,0,.35)}
.hero-copy .lead{font-size:23px;font-weight:500;line-height:38px;top:331px}
.hero-copy .sub{font-size:17px;font-weight:300;line-height:28.5px;top:405px}

/* intro */
.intro{top:662px;left:0;width:1200px;height:1463px;
  background:
    radial-gradient(ellipse 300px 560px at 1000px 720px,rgba(150,120,95,.22) 0%,rgba(150,120,95,.10) 50%,rgba(255,255,255,0) 100%),
    linear-gradient(to bottom,#ffffff 0%,#f3f5ef 22%,#e9eee2 50%,#edf1e7 70%,#ffffff 100%)}
.mark{width:16px;height:16px;border-radius:50%;background:var(--brand);left:592px}
.h2{font-size:39px;font-weight:500;color:var(--ink)}
.body{font-size:13.5px;line-height:28.5px;color:var(--ink)}
.btn{position:absolute;background:var(--brand);color:var(--white);font-size:14px;display:flex;
  align-items:center;justify-content:center;gap:22px;text-decoration:none;letter-spacing:.2px}
.btn .arrows{font-size:12px;letter-spacing:2px}

.gallery{top:1499px;left:112px;width:976px;display:grid;grid-template-columns:repeat(3,320px);
  grid-auto-rows:279px;gap:8px}
.gallery div{border-radius:2px;box-shadow:0 1px 3px rgba(0,0,0,.12)}
.g1{background:linear-gradient(to bottom,#f0d6b4 0%,#d9b89a 30%,#a99a8a 52%,#7d7560 70%,#5d5442 100%)}
.g2{background:radial-gradient(ellipse at 50% 20%,#ffd57a 0%,rgba(255,213,122,0) 50%),linear-gradient(to bottom,#e9b34d 0%,#c99336 45%,#a67c2c 75%,#8d6a2a 100%)}
.g3{background:linear-gradient(to bottom,#6d7a58 0%,#b99a3c 30%,#8a6a3a 55%,#a45a32 80%,#8c4c2c 100%)}
.g4{background:linear-gradient(to bottom,#35602c 0%,#55834a 25%,#d4b78c 50%,#8a72b8 75%,#5a45a0 100%)}
.g5{background:linear-gradient(to bottom,#2d5226 0%,#4a6a30 25%,#7d4a2a 50%,#6a3e24 65%,#5c9a3e 88%,#4d8a34 100%)}
.g6{background:linear-gradient(to bottom,#eef0f2 0%,#e2e5e8 45%,#c6ccc0 62%,#8ea45a 78%,#6e8a3a 100%)}

/* cause band */
.cause{top:2145px;left:0;width:1200px;height:440px;
  background:
    radial-gradient(ellipse 260px 220px at 300px 250px,rgba(120,62,30,.45) 0%,rgba(120,62,30,.15) 55%,rgba(0,0,0,0) 100%),
    linear-gradient(to bottom,#a9b1ab 0%,#8e9c88 14%,#6f8a58 26%,#5a9240 45%,#4a8a36 70%,#3e7a2e 100%)}
.cause-shade{top:2145px;left:560px;width:640px;height:440px;background:linear-gradient(to right,rgba(0,0,0,0),rgba(20,50,15,.18))}
.cause-copy{left:600px;width:494px;text-align:center;color:var(--white);text-shadow:0 1px 3px rgba(0,0,0,.3)}

/* contact */
.card{top:2860px;left:110px;width:978px;height:435px;
  background:
    radial-gradient(ellipse 320px 260px at 700px 200px,rgba(170,165,160,.22) 0%,rgba(255,255,255,0) 100%),
    linear-gradient(120deg,#f3f3f3,#ebebec 50%,#e4e4e5);box-shadow:0 0 18px rgba(0,0,0,.18)}
.info{font-size:18.5px;color:var(--ink)}
.info svg{position:absolute}
.field{left:601px;width:422px;border-bottom:1px solid var(--rule);height:31px;font-size:14.5px;color:#8a8a8a}
.submit{top:3197px;left:602px;width:224px;height:45px;background:var(--brand);color:var(--white);
  font-size:20px;font-weight:600;display:flex;align-items:center;justify-content:center;letter-spacing:.5px}
.card-mark{top:3170px;left:200px;width:40px;height:40px;border-radius:50%;background:rgba(179,19,31,.25)}

/* footer */
.footer{top:3402px;left:0;width:1200px;height:249px;background:var(--footer)}
.social{width:36px;height:36px;border:1.5px solid var(--white);border-radius:50%;top:3465px}
.fnav a{position:absolute;top:3529px;color:var(--white);font-size:15px;text-decoration:none;white-space:nowrap}
.copy{top:3570px;font-size:13px;color:#e5e5e5}
</style>
</head>
<body>

<header>
  <div class="abs hero" role="img" aria-label="Herd of horses galloping through dust under a stormy sky"></div>
  <div class="abs hero-shade"></div>
  <div class="abs brand-card">
    <div class="dot"></div>
    <div class="brand-name">Fernvale Quillstone Heritage</div>
  </div>
  <nav class="nav">
    <a style="left:443px">HOME</a>
    <a style="left:538px">ABOUT</a>
    <a style="left:640px">ADOPT</a>
    <a style="left:741px">HORSES</a>
    <a style="left:850px">DONATE/SHOP</a>
    <a style="left:1012px">CONTACT</a>
  </nav>
  <div class="hero-copy">
    <p class="abs center lead">We support and develop retired thoroughbred racehorses<br>for their next chapter in life</p>
    <p class="abs center sub">Retire. Retrain. Rehome.<br>Fernvale Quillstone Heritage Society (FQHS)<br>is a registered not-for-profit organization in Fernvale.</p>
  </div>
</header>

<section>
  <div class="abs intro" role="img" aria-label="Faded photo of a rider on horseback in a misty field"></div>

  <div class="abs mark" style="top:758px"></div>
  <h2 class="abs center h2" style="top:834px">What is Thoroughbred Aftercare?</h2>
  <p class="abs center body" style="top:904px">The health, safety and welfare of our equine athletes does not end at the finish line, and retirement and<br>aftercare are critical to the success of the racing industry.</p>
  <p class="abs center body" style="top:988px">Aftercare is the safe placement of racehorses after their careers as racehorse are completed. Some horses<br>might retire to the breeding shed or broodmare bands, while others are retrained for second careers.</p>
  <a class="btn" style="top:1064px;left:466px;width:268px;height:43px">LEARN MORE ABOUT US <span class="arrows">&gt;&gt;</span></a>

  <div class="abs mark" style="top:1242px"></div>
  <h2 class="abs center h2" style="top:1312px">Adopt a Horse</h2>
  <p class="abs center body" style="top:1372px">Fernvale Quillstone Heritage is committed to helping match you with the perfect horse.</p>
  <a class="btn" style="top:1416px;left:496px;width:208px;height:42px">ADOPT NOW <span class="arrows">&gt;&gt;</span></a>

  <div class="abs gallery">
    <div class="g1" role="img" aria-label="Grey horse standing by a fence at sunset"></div>
    <div class="g2" role="img" aria-label="Chestnut horse galloping in golden grass"></div>
    <div class="g3" role="img" aria-label="Horse trotting through autumn leaves"></div>
    <div class="g4" role="img" aria-label="Palomino horse among purple lupins"></div>
    <div class="g5" role="img" aria-label="Two bay horses grazing in a paddock"></div>
    <div class="g6" role="img" aria-label="Horse running on a grassy hill"></div>
  </div>
</section>

<section>
  <div class="abs cause" role="img" aria-label="Jockey riding a racehorse on a green turf track"></div>
  <div class="abs cause-shade"></div>
  <div class="abs mark" style="top:2230px;left:838px"></div>
  <div class="abs cause-copy" style="top:2315px">
    <h2 style="font-size:39px;font-weight:500">Make a Difference</h2>
    <p style="font-size:15px;line-height:30px;margin-top:12px">Lorem Ipsum is simply dummy text of the printing and<br>typesetting industry. Lorem Ipsum has been the industry's<br>standard dummy text ever since the 1500s,</p>
  </div>
  <a class="btn" style="top:2487px;left:726px;width:242px;height:42px">MORE WAYS TO GIVE <span class="arrows">&gt;&gt;</span></a>
</section>

<section>
  <div class="abs mark" style="top:2700px"></div>
  <h2 class="abs center h2" style="top:2770px">Have a Question?</h2>

  <div class="abs card" role="img" aria-label="Faded photo of riders with a white horse"></div>
  <div class="abs card-mark"></div>

  <div class="abs info" style="top:2910px;left:177px">
    <svg width="24" height="24" viewBox="0 0 24 24" style="left:0;top:2px"><path fill="#b3131f" d="M6.6 10.8c1.4 2.8 3.8 5.1 6.6 6.6l2.2-2.2c.3-.3.7-.4 1-.2 1.1.4 2.3.6 3.6.6.6 0 1 .4 1 1V20c0 .6-.4 1-1 1C10.6 21 3 13.4 3 4c0-.6.4-1 1-1h3.5c.6 0 1 .4 1 1 0 1.3.2 2.5.6 3.6.1.3 0 .7-.2 1z"/></svg>
    <span style="position:absolute;left:47px;white-space:nowrap">Phone: &nbsp;555-014-2270</span>
  </div>
  <div class="abs info" style="top:2955px;left:177px">
    <svg width="24" height="18" viewBox="0 0 24 18" style="left:0;top:6px"><rect width="24" height="18" rx="2" fill="#b3131f"/><path d="M2 3l10 7 10-7" fill="none" stroke="#fff" stroke-width="2"/></svg>
    <span style="position:absolute;left:48px;white-space:nowrap">info@fernvaleqhs.org</span>
  </div>
  <div class="abs info" style="top:3013px;left:177px">
    <svg width="20" height="26" viewBox="0 0 20 26" style="left:0;top:2px"><path fill="#b3131f" d="M10 0C4.5 0 0 4.4 0 9.8 0 17 10 26 10 26s10-9 10-16.2C20 4.4 15.5 0 10 0zm0 13.5a3.7 3.7 0 110-7.4 3.7 3.7 0 010 7.4z"/></svg>
    <span style="position:absolute;left:42px;white-space:nowrap;line-height:27px">42 Marlow Crescent<br>Ostrel Vale 7731<br>Brennick</span>
  </div>

  <div class="abs field" style="top:2918px">Name</div>
  <div class="abs field" style="top:2990px">Phone</div>
  <div class="abs field" style="top:3054px">Email</div>
  <div class="abs field" style="top:3127px">Message</div>
  <div class="abs submit">Submit Now</div>
</section>

<footer>
  <div class="abs footer"></div>
  <div class="abs social" style="left:522px"></div>
  <div class="abs social" style="left:562px"></div>
  <div class="abs social" style="left:602px"></div>
  <div class="abs social" style="left:642px"></div>
  <nav class="fnav">
    <a style="left:277px">HOME</a>
    <a style="left:372px">ABOUT</a>
    <a style="left:474px">ADOPT</a>
    <a style="left:575px">HORSES</a>
    <a style="left:684px">DONATE/SHOP</a>
    <a style="left:846px">CONTACT</a>
  </nav>
  <p class="abs center copy">Fernvale Quillstone Heritage © 2021 All Rights Reserved.</p>
</footer>

</body>
</html>
```